Moravel Aesthetic Doctor

I require an elegant, luxurious looking business card for my aesthetic business. I am a doctor and that will set me aside from competitors. I am planning to provide home and spa based treatments to clients with high expectations. I have attached my logo.

```html
<!DOCTYPE html>
<html lang="en">
<head>
<meta charset="utf-8">
<title>Moravel Aesthetic Doctor – Business Card</title>
<link href="https://fonts.googleapis.com/css2?family=Arimo:wght@400;700&display=swap" rel="stylesheet">
<style>
  :root {
    --bg-deep: #050506;
    --bg-mid: #16171a;
    --card: #2a2b2f;
    --card-dark: #222326;
    --edge: #5ec3ec;
    --accent: #4fb6e6;
    --text-light: #e9eaec;
    --text-grey: #a9abaf;
    --rule: #55575c;
  }
  * { box-sizing: border-box; margin: 0; padding: 0; }
  html, body { width: 1200px; height: 820px; overflow: hidden; }
  body {
    background: radial-gradient(ellipse at 50% 45%, var(--bg-mid) 0%, var(--bg-deep) 75%);
    font-family: "Arimo", Arial, sans-serif;
    position: relative;
  }
  .card {
    position: absolute;
    top: 250px;
    width: 540px;
    height: 310px;
    background: linear-gradient(160deg, var(--card) 0%, var(--card-dark) 100%);
    border-bottom: 3px solid var(--edge);
    border-left: 2px solid var(--edge);
    box-shadow: 0 18px 40px rgba(0,0,0,.7);
  }
  .card--front { left: 40px; }
  .card--back { left: 620px; }

  /* Front */
  .brand {
    position: absolute;
    top: 46px;
    right: 60px;
    display: flex;
    align-items: center;
    gap: 14px;
  }
  .brand__dot {
    width: 44px; height: 44px;
    border-radius: 50%;
    border: 2px solid var(--text-grey);
  }
  .brand__name {
    color: var(--text-light);
    font-weight: 400;
    font-size: 20px;
    letter-spacing: 2px;
    line-height: 1.2;
    text-transform: uppercase;
  }
  .social {
    position: absolute;
    top: 138px;
    right: 40px;
    display: flex;
    gap: 8px;
  }
  .social__dot {
    width: 20px; height: 20px;
    border-radius: 50%;
    border: 1.5px solid var(--accent);
  }
  .rule-top {
    position: absolute;
    top: 152px; left: 200px; right: 92px;
    height: 1px; background: var(--rule);
  }
  .person {
    position: absolute;
    left: 40px; top: 168px;
  }
  .person__name {
    color: var(--text-grey);
    font-weight: 700;
    font-size: 20px;
  }
  .person__creds {
    color: var(--accent);
    font-weight: 400;
    font-size: 14px;
  }
  .person__diploma {
    color: var(--accent);
    font-size: 14px;
    margin-top: 3px;
  }
  .rule-bottom {
    position: absolute;
    top: 218px; left: 40px; width: 250px;
    height: 1px; background: var(--rule);
  }
  .contact {
    position: absolute;
    left: 40px; top: 230px;
    list-style: none;
    color: var(--text-grey);
    font-size: 14px;
  }
  .contact li {
    display: flex; align-items: center; gap: 10px;
    height: 21px;
  }
  .contact svg { width: 14px; height: 14px; }

  /* Back */
  .motif {
    position: absolute;
    top: 20px; right: 40px;
    width: 240px; height: 170px;
    border-radius: 50%;
    background: radial-gradient(ellipse at 60% 45%, #3b3c41 0%, #2f3034 55%, rgba(42,43,47,0) 75%);
  }
  .services {
    position: absolute;
    left: 48px; top: 150px;
    list-style: none;
    color: var(--text-light);
    font-size: 13px;
    letter-spacing: .4px;
    text-transform: uppercase;
  }
  .services li {
    display: flex; align-items: center; gap: 8px;
    height: 22px;
  }
  .services li::before {
    content: "";
    width: 7px; height: 7px;
    border-radius: 50%;
    background: var(--accent);
  }
</style>
</head>
<body>

<section class="card card--front" aria-label="Business card front">
  <div class="brand">
    <span class="brand__dot"></span>
    <div class="brand__name">Moravel<br>Aesthetic Doctor</div>
  </div>

  <div class="social" aria-label="Social profiles">
    <span class="social__dot"></span>
    <span class="social__dot"></span>
  </div>
  <div class="rule-top"></div>

  <div class="person">
    <p><span class="person__name">Dr Elena Varga</span> <span class="person__creds">MRCPCH MD</span></p>
    <p class="person__diploma">Australasian Diploma of Aesthetic Medicine</p>
  </div>
  <div class="rule-bottom"></div>

  <ul class="contact">
    <li>
      <svg viewBox="0 0 16 16" fill="none" stroke="var(--accent)" stroke-width="1.6"><path d="M3 2l3 1 1 3-2 1.5a8 8 0 0 0 3.5 3.5L10 9l3 1 1 3-2 1.5C6 14 2 10 1.5 4z"/></svg>
      0800 555 014
    </li>
    <li>
      <svg viewBox="0 0 16 16" fill="none" stroke="var(--accent)" stroke-width="1.6"><rect x="1.5" y="3.5" width="13" height="9"/><path d="M1.5 3.5L8 9l6.5-5.5"/></svg>
      elena@moravel.co.nz
    </li>
    <li>
      <svg viewBox="0 0 16 16" fill="none" stroke="var(--accent)" stroke-width="1.4"><circle cx="8" cy="8" r="6.5"/><ellipse cx="8" cy="8" rx="3" ry="6.5"/><path d="M1.5 8h13M3 4.5h10M3 11.5h10"/></svg>
      www.moravel.co.nz
    </li>
  </ul>
</section>

<section class="card card--back" aria-label="Business card back">
  <div class="motif" role="img" aria-label="Faint embossed decorative motif area"></div>
  <ul class="services">
    <li>Dermal Injectables</li>
    <li>Plasma Facials</li>
    <li>Microneedling</li>
    <li>Skin Boosters</li>
    <li>Excessive Sweating</li>
    <li>Home and Spa Based Treatments</li>
  </ul>
</section>

</body>
</html>
```